Belvascotravel.com web design project + logo design

Hi,

We are a Russian online tour operator - sunkettle.com

We are looking to tranmsfer our domain to belvascotravel.com. The website and logo need to be belvascoesque - we are not looking to change our functionality, but we need to make the website much more attracitve to clients, much more wild looking but at the same time remaining a professional travel company.

The main concept of the website should be innovative travel (as belvasco was an innovator). Alternatively, you could go down the artist route and go down the draw / design your own tour road.

On our website the customer is able to combine travel services (hotels, flights, Visa services, and soon chauffeur, car rental etc...) put it into their basket (the basket definitely has to look better than it is at the moment) and pay for it in one go by card.

We are also stressin our customer support with web chat, call centre etc... (call centre number at the top of the page)

We aim to provide an easy user experience, but we need to make it have some more style, so I will be waiting for what you guys can come up with.
Let me know if you have any questions - skype is: mrdolbarin

Industry/Entity Type

It Company

Requirements
Must have
• It is quite a simple task - to take the existing website sunkettle.com and belvascosize it to create belvascotravel.com, the functionality of the website will remain the same and there are not many pages in the website. Homepage, Checkout step1, Checkout step 2 (you can view both of these if you select a service) and the generic pages for T&C''s, Privacy policy etc...

IMPORTANT UPDATE

We are also looking at how the search results will look in the designs, (please do a search on our website for hotel / flight)

```html
<!DOCTYPE html>
<html lang="en">
<head>
<meta charset="utf-8">
<title>Belvasco Travel</title>
<link href="https://fonts.googleapis.com/css2?family=Open+Sans:wght@300;400;600;700&display=swap" rel="stylesheet">
<style>
:root{
  --blue:#2b8fd3;
  --blue-light:#d6ebf8;
  --green:#4aa83a;
  --ink:#333;
  --muted:#777;
  --line:#e2e2e2;
  --paper:#fff;
  --soft:#f4f4f4;
  --footer:#2e2e2e;
  --footer-deep:#222;
}
*{margin:0;padding:0;box-sizing:border-box}
html,body{width:789px;height:1200px;overflow:hidden}
body{font-family:"Open Sans",Arial,sans-serif;color:var(--ink);background:var(--paper);position:relative;font-size:9px}

.site-header{position:absolute;top:0;left:0;width:789px;height:78px;display:flex;align-items:center;justify-content:space-between;padding:0 22px;border-bottom:3px solid var(--blue)}
.brand-name{font-size:16px;font-weight:600;color:var(--ink)}
.main-nav{display:flex;gap:26px;margin-top:14px}
.main-nav a{font-size:10px;color:#555;text-decoration:none;padding-bottom:6px}
.main-nav a.active{color:var(--green);border-bottom:2px solid var(--green)}

.hero{position:absolute;top:78px;left:0;width:789px;height:270px;background:var(--soft)}
.search-box{position:absolute;left:20px;top:10px;width:186px;height:246px;background:var(--blue-light);border:1px solid #b9d9ee;border-radius:4px;padding:10px}
.search-box h2{font-size:12px;color:var(--blue);font-weight:700;margin-bottom:8px}
.field{height:20px;background:#fff;border:1px solid #c7d9e6;border-radius:2px;margin-bottom:7px;font-size:8px;color:#888;padding:4px 6px;white-space:nowrap;overflow:hidden}
.field-row{display:flex;gap:6px}
.field-row .field{flex:1}
.proceed{display:block;width:90px;margin:8px auto 0;height:22px;background:var(--blue);color:#fff;font-size:9px;font-weight:700;text-align:center;line-height:22px;border-radius:3px}
.slider{position:absolute;left:216px;top:10px;width:553px;height:246px;background:linear-gradient(180deg,#7ab6d8 0%,#2e7fa8 45%,#1f4d5c 75%,#c8a27a 100%);border-radius:2px}
.arrow{position:absolute;width:22px;height:22px;border-radius:50%;background:var(--green);display:flex;align-items:center;justify-content:center}
.arrow.dark{background:#333}

.welcome{position:absolute;top:348px;left:0;width:789px;height:272px;padding:26px 22px}
.welcome h1{font-size:19px;font-weight:300;color:var(--blue);margin-bottom:12px}
.welcome p{width:430px;font-size:8.5px;line-height:1.6;color:var(--muted);margin-bottom:10px}
.location-photo{position:absolute;left:512px;top:34px;width:186px;height:186px;border-radius:50%;background:linear-gradient(160deg,#9fd0ef,#f0d9b0);border:4px solid #fff;box-shadow:0 0 0 1px var(--line)}
.location-caption{position:absolute;left:478px;top:232px;width:254px;text-align:center;font-size:9px;font-weight:600;color:#555}

.services{position:absolute;top:620px;left:0;width:789px;height:228px;border-top:1px solid var(--line);padding:16px 22px}
.services h2{font-size:15px;font-weight:600;color:#444;border-left:4px solid var(--green);padding-left:8px;line-height:1}
.services .sub{font-size:8px;color:var(--muted);padding-left:12px;margin:4px 0 12px}
.service-menu{position:absolute;left:22px;top:66px;width:158px}
.service-menu li{list-style:none;height:26px;line-height:26px;font-size:9.5px;color:#555;background:#f0f0f0;border-bottom:1px solid #fff;padding-left:26px;position:relative}
.service-menu li::before{content:"";position:absolute;left:9px;top:9px;width:8px;height:8px;background:#999}
.service-menu li.active{background:var(--green);color:#fff;font-weight:700}
.service-menu li.active::before{background:#fff}
.service-text{position:absolute;left:198px;top:66px;width:360px}
.service-text p{font-size:8.5px;line-height:1.6;color:var(--muted);margin-bottom:8px}
.service-text a{font-size:9px;color:var(--blue);font-weight:600;text-decoration:none}
.advisor-photo{position:absolute;left:586px;top:28px;width:180px;height:186px;background:linear-gradient(180deg,#eef1f4,#c9d2dc)}

.trips{position:absolute;top:848px;left:0;width:789px;height:184px;border-top:1px solid var(--line);padding:12px 22px}
.trips-title{display:flex;align-items:center;justify-content:center;gap:12px;font-size:9px;color:#555;margin-bottom:10px}
.trip-grid{display:flex;gap:14px}
.trip-card{width:176px}
.trip-photo{height:78px;border-radius:2px}
.trip-card h3{font-size:10px;color:var(--blue);font-weight:600;margin:6px 0 3px}
.trip-card p{font-size:7.5px;line-height:1.5;color:var(--muted)}

.site-footer{position:absolute;top:1032px;left:0;width:789px;height:168px;background:var(--footer);color:#bbb}
.footer-cols{display:flex;padding:12px 22px 0;gap:20px;height:144px}
.footer-col h4{font-size:9.5px;color:#fff;font-weight:700;margin-bottom:6px}
.footer-col li{list-style:none;font-size:7.5px;line-height:1.6}
.col-dest{width:150px}.col-map{width:140px}.col-test{width:200px}.col-contact{width:200px}
.testimonial{display:flex;gap:6px}
.avatar{width:28px;height:28px;background:#777;flex:none}
.testimonial p{font-size:7.5px;line-height:1.5}
.testimonial strong{display:block;color:#fff;font-size:8px}
.footer-bar{height:24px;background:var(--footer-deep);display:flex;justify-content:space-between;align-items:center;padding:0 22px;font-size:7.5px;color:#999}
</style>
</head>
<body>

<header class="site-header">
  <div class="brand"><span class="brand-name">Belvasco Travel</span></div>
  <nav class="main-nav">
    <a class="active" href="#">Home</a><a href="#">Destinations</a><a href="#">Activities</a><a href="#">Trip Styles</a><a href="#">Responsible Travel</a>
  </nav>
</header>

<section class="hero">
  <form class="search-box">
    <h2>FIND A PLACE TO STAY</h2>
    <div class="field">Where do you want to go?</div>
    <div class="field">Region</div>
    <div class="field-row"><div class="field">Check In</div><div class="field">Check Out</div></div>
    <div class="field-row"><div class="field">Room</div><div class="field">Nights</div></div>
    <div class="field-row"><div class="field">Adults</div><div class="field">Children</div></div>
    <div class="field">Budget range</div>
    <span class="proceed">PROCEED</span>
  </form>
  <div class="slider" role="img" aria-label="Tropical seaside resort at dusk with palm trees and calm water">
    <span class="arrow" style="left:10px;top:112px"><svg width="8" height="10" viewBox="0 0 8 10"><path d="M6 1L2 5l4 4" stroke="#fff" stroke-width="2" fill="none"/></svg></span>
    <span class="arrow" style="right:10px;top:112px"><svg width="8" height="10" viewBox="0 0 8 10"><path d="M2 1l4 4-4 4" stroke="#fff" stroke-width="2" fill="none"/></svg></span>
  </div>
</section>

<section class="welcome">
  <h1>Welcome to Belvasco Travel</h1>
  <p>We build journeys that fit the way you like to travel. Pick a hotel, add a flight, sort your visa and pay for everything in one simple step. Our team checks every partner so each stay feels easy and safe.</p>
  <p>From quiet beaches to busy capitals, we help you shape a trip of your own. Combine services, compare options and keep all your plans in one clear basket, with real people ready to help by chat or phone.</p>
  <p>Travel with ideas, not limits. Draw your own route and let us handle the details.</p>
  <div class="location-photo" role="img" aria-label="Traveller relaxing on a sunny beach"></div>
  <span class="arrow dark" style="left:500px;top:116px"><svg width="8" height="10" viewBox="0 0 8 10"><path d="M6 1L2 5l4 4" stroke="#fff" stroke-width="2" fill="none"/></svg></span>
  <span class="arrow dark" style="left:688px;top:116px"><svg width="8" height="10" viewBox="0 0 8 10"><path d="M2 1l4 4-4 4" stroke="#fff" stroke-width="2" fill="none"/></svg></span>
  <div class="location-caption">SELECT YOUR DESIRE LOCATION</div>
</section>

<section class="services">
  <h2>Our Services</h2>
  <div class="sub">Everything you need for your trip in one place</div>
  <ul class="service-menu">
    <li class="active">Visa Service</li>
    <li>Hotel Service</li>
    <li>Other Services</li>
  </ul>
  <div class="service-text">
    <p>Our visa desk prepares your papers, checks every form and tracks your application until it is ready. You get clear steps, fixed prices and updates at each stage so nothing is missed before you fly.</p>
    <p>Book the visa together with your hotel and flights, then pay for the whole package in one go. Our advisers are on hand by chat or phone whenever you have a question.</p>
    <a href="#">View Detail</a>
  </div>
  <div class="advisor-photo" role="img" aria-label="Travel adviser in a suit"></div>
</section>

<section class="trips">
  <div class="trips-title">
    <svg width="8" height="10" viewBox="0 0 8 10"><path d="M6 1L2 5l4 4" stroke="#999" stroke-width="1.5" fill="none"/></svg>
    Some Of Our Client Trip Photos
    <svg width="8" height="10" viewBox="0 0 8 10"><path d="M2 1l4 4-4 4" stroke="#999" stroke-width="1.5" fill="none"/></svg>
  </div>
  <div class="trip-grid">
    <div class="trip-card"><div class="trip-photo" role="img" aria-label="Beach with sun umbrellas" style="background:linear-gradient(180deg,#8fc9ec,#e9d6ad)"></div><h3>January Trip</h3><p>Warm sand and clear water for a winter break by the sea.</p></div>
    <div class="trip-card"><div class="trip-photo" role="img" aria-label="Group jumping on a beach" style="background:linear-gradient(180deg,#5eb3e6,#f1dcaa)"></div><h3>March Trip</h3><p>A group getaway full of sun, games and long walks.</p></div>
    <div class="trip-card"><div class="trip-photo" role="img" aria-label="Friends posing outdoors" style="background:linear-gradient(180deg,#9fd4a4,#d8c2a0)"></div><h3>August Trip</h3><p>Summer days out with friends in green open country.</p></div>
    <div class="trip-card"><div class="trip-photo" role="img" aria-label="Tropical island shoreline" style="background:linear-gradient(180deg,#7cc3e8,#3a9bb8)"></div><h3>December Trip</h3><p>Island calm to close the year under palm trees.</p></div>
  </div>
</section>

<footer class="site-footer">
  <div class="footer-cols">
    <div class="footer-col col-dest"><h4>DESTINATIONS</h4><ul><li>Europe</li><li>North America</li><li>South America</li><li>Africa</li><li>Asia</li><li>Australia</li></ul></div>
    <div class="footer-col col-map"><h4>SITE MAP</h4><ul><li>Home</li><li>Activities</li><li>Trip Styles</li><li>Responsible Travel</li></ul></div>
    <div class="footer-col col-test"><h4>TESTIMONIALS</h4>
      <div class="testimonial"><div class="avatar" role="img" aria-label="Client portrait"></div><p><strong>Anna Petrova</strong>"Booking the hotel and visa together saved us time, and the support team answered every question quickly."</p></div>
    </div>
    <div class="footer-col col-contact"><h4>CONTACT INFORMATIONS</h4><ul><li>E-mail: info@website.com</li><li>Phone: +01 23 456 789</li><li>Working hours</li><li>Mon - Fri: 09:00 - 18:00</li><li>Sat: 10:00 - 16:00</li><li>Sun: 10:00 - 14:00</li></ul></div>
  </div>
  <div class="footer-bar"><span>Copyright 2015 Website Name. All Rights Reserved</span><span>Privacy Policy | Terms &amp; Condition</span></div>
</footer>

</body>
</html>
```